Summit Ridge Business Card

Side 1: Summit Ridge Logo (logo without Maltese cross) with industrial rope rescue related theme. Our company services - TRAINING - Fire Training, Confined Space Rescue Training, Rope Rescue training, Hazmat Training, Incident Command, EMS, Pump Operations Training. Website - summitridgeexample.com.
Side 2: Summit Ridge Fire Department Logo (logo with Maltese cross) with Firefighter related theme. Company (division) services - FIELD SERVICES - Fire Department, Stand-by Rescue, Safety, EMS, Planning. "Supporting the Emergency Response Community Since 1967"

Add contact information wherever it makes since (Name, Email, Phone).
I would like it to represent the Summit Ridge Fire Department Logo as a division not as a separate entity without saying it, possibly by depicting it in the background of Side 2 instead of being a standalone picture like the logo on Side 1.

```html
<!DOCTYPE html>
<html lang="en">
<head>
<meta charset="utf-8">
<title>Summit Ridge Business Card</title>
<link href="https://fonts.googleapis.com/css2?family=Arimo:wght@400;700&family=Archivo+Black&display=swap" rel="stylesheet">
<style>
  :root {
    --red: #e0141b;
    --ink: #1f1f21;
    --charcoal: #3c3c3f;
    --charcoal-dark: #343437;
    --paper: #f7f7f6;
    --bg: #d9d9d9;
    --faint: #47474b;
  }
  * { box-sizing: border-box; margin: 0; padding: 0; }
  html, body { width: 1200px; height: 960px; overflow: hidden; background: var(--bg); }
  body { font-family: "Arimo", Arial, sans-serif; position: relative; }

  .card {
    position: absolute; left: 210px; width: 780px; height: 440px;
    border-radius: 22px; overflow: hidden;
    box-shadow: 0 6px 18px rgba(0,0,0,.18);
  }

  /* Back side */
  .card--back { top: 27px; background: var(--charcoal); color: #fff; }
  .back-mark-dot {
    position: absolute; left: 60px; top: 60px; width: 300px; height: 300px;
    border-radius: 50%; background: var(--faint); opacity: .35;
  }
  .back-mark {
    position: absolute; left: 40px; top: 150px;
    font-family: "Archivo Black", Arial, sans-serif; font-size: 64px;
    color: var(--faint); letter-spacing: 2px; line-height: 1;
  }
  .services { position: absolute; left: 440px; top: 90px; }
  .services h2 {
    font-family: "Archivo Black", Arial, sans-serif; font-size: 26px;
    font-weight: 400; letter-spacing: 1px; margin-bottom: 14px;
  }
  .services ul { list-style: none; font-size: 19px; line-height: 1.3; margin-left: 18px; }
  .services li::before { content: "•"; margin-right: 8px; }
  .services .tagline { margin: 22px 0 0 34px; font-size: 19px; line-height: 1.3; }

  /* Front side */
  .card--front { top: 493px; background: var(--paper); color: var(--ink); }
  .contact { position: absolute; left: 46px; top: 46px; }
  .contact .name {
    font-family: "Archivo Black", Arial, sans-serif; font-size: 28px;
    color: var(--red); font-weight: 400; line-height: 1;
  }
  .contact p { font-size: 20px; line-height: 24px; margin-top: 3px; }
  .contact .phone { display: flex; align-items: center; gap: 10px; }
  .contact .phone svg { width: 17px; height: 17px; }

  .brand { position: absolute; right: 46px; top: 52px; width: 320px; text-align: center; }
  .brand .square { width: 52px; height: 52px; background: var(--red); margin: 0 auto 12px; }
  .brand .wordmark {
    font-family: "Archivo Black", Arial, sans-serif; font-size: 30px;
    color: var(--red); letter-spacing: 1px; line-height: 1; white-space: nowrap;
  }

  .divider { position: absolute; left: 40px; right: 40px; top: 206px; border-top: 1.5px solid var(--ink); }
  .address { position: absolute; right: 46px; top: 216px; text-align: right; font-size: 20px; line-height: 26px; }
  .training { position: absolute; left: 40px; top: 272px; width: 700px; font-size: 18px; line-height: 1.35; }

  .band { position: absolute; left: 0; bottom: 0; width: 780px; height: 100px; }
  .website {
    position: absolute; right: 56px; bottom: 18px;
    color: #fff; font-size: 21px; letter-spacing: .5px;
  }
</style>
</head>
<body>

<section class="card card--back" aria-label="Card back: field services">
  <div class="back-mark-dot" aria-hidden="true"></div>
  <div class="back-mark" aria-hidden="true">SUMMIT<br>RIDGE</div>
  <div class="services">
    <h2>FIELD SERVICES</h2>
    <ul>
      <li>Fire Department</li>
      <li>Stand-by Rescue</li>
      <li>Safety</li>
      <li>EMS</li>
      <li>Planning</li>
    </ul>
    <p class="tagline">Supporting the Emergency<br>Response Community<br>Since 1967</p>
  </div>
</section>

<section class="card card--front" aria-label="Card front: contact">
  <div class="contact">
    <h1 class="name">DANIEL HARPER</h1>
    <p class="role">President</p>
    <p class="email">daniel@summitridgeexample.com</p>
    <p class="phone">
      <svg viewBox="0 0 24 24" aria-hidden="true"><path fill="#e0141b" d="M6.6 10.8a15 15 0 0 0 6.6 6.6l2.2-2.2a1 1 0 0 1 1-.25 11.4 11.4 0 0 0 3.6.57 1 1 0 0 1 1 1V20a1 1 0 0 1-1 1A17 17 0 0 1 3 4a1 1 0 0 1 1-1h3.5a1 1 0 0 1 1 1c0 1.25.2 2.45.57 3.57a1 1 0 0 1-.25 1z"/></svg>
      +1 555-014-0192
    </p>
    <p class="phone">
      <svg viewBox="0 0 24 24" aria-hidden="true"><rect x="6" y="2" width="12" height="20" rx="2" fill="none" stroke="#e0141b" stroke-width="2.2"/></svg>
      +1 555-014-0192
    </p>
  </div>

  <div class="brand">
    <div class="square" aria-hidden="true"></div>
    <div class="wordmark">SUMMIT RIDGE</div>
  </div>

  <div class="divider" aria-hidden="true"></div>

  <p class="address">418 Harbor Ln., Lakeview<br>TX, United States, 75001</p>

  <p class="training">TRAINING - Fire Training, Confined Space Rescue Training, Rope Rescue training, Hazmat Training, Incident Command, EMS, Pump Operations Training.</p>

  <svg class="band" viewBox="0 0 780 120" preserveAspectRatio="none" aria-hidden="true">
    <polygon points="0,12 430,62 480,62 440,120 0,120" fill="var(--red)"/>
    <polygon points="0,50 420,100 460,100 440,120 0,120" fill="var(--charcoal-dark)"/>
    <polygon points="475,52 780,52 780,120 430,120" fill="var(--charcoal)"/>
  </svg>
  <p class="website">www.summitridgeexample.com</p>
</section>

</body>
</html>
```